Healthcare and Professional IT Services Company need a redesigned business card

We are a IT Services company that targets small medical practices and professional business such as Attorneys, Accounts, Architects etc. We want to communicate a professional yet friendly image using recent logo redesign here on ArtHarbor. Like to see the colors blue and orange in the design. Must use the Tall Pine Computing as displayed in the new logo - then also want to incorporate the fish logo as well.

Target Market(s)

Small medical and professional services

Industry/Entity Type

It Company

Contact Information for Business Card

The usual stuff, place for name address phone website. Also maybe our tagline which is "hooked on technology"

Requirements
Must have
• My new logo and the fish somewhere on the card

```html
<!DOCTYPE html>
<html lang="en">
<head>
<meta charset="utf-8">
<title>Tall Pine Computing – Business Card</title>
<link rel="stylesheet" href="https://fonts.googleapis.com/css2?family=Quicksand:wght@500&family=Open+Sans:wght@400&display=swap">
<style>
  :root {
    --page-bg: #e9e6e1;
    --card-white: #f7f8f9;
    --brand-blue: #4169b0;
    --brand-sky: #5bc3e6;
    --ink-white: #ffffff;
    --fish-teal: #3c8fb4;
    --fish-orange: #e07a3a;
  }
  html, body {
    margin: 0;
    width: 1200px;
    height: 902px;
    overflow: hidden;
    background: var(--page-bg);
  }
  .card {
    position: absolute;
    left: 75px;
    top: 151px;
    width: 1050px;
    height: 600px;
    background: var(--card-white);
    box-shadow: 0 4px 18px rgba(0,0,0,0.18);
    overflow: hidden;
  }
  .card-wave {
    position: absolute;
    inset: 0;
  }
  .fish-mark {
    position: absolute;
    left: 110px;
    top: 170px;
    width: 190px;
    height: 130px;
    border-radius: 50% 45% 45% 50%;
    background: linear-gradient(90deg, var(--fish-orange) 0%, var(--fish-teal) 45%, #5aa7c9 100%);
  }
  .company-name {
    position: absolute;
    left: 330px;
    top: 88px;
    margin: 0;
    font-family: "Quicksand", sans-serif;
    font-weight: 500;
    font-size: 56px;
    line-height: 1.1;
    color: var(--brand-blue);
    letter-spacing: 0.5px;
    white-space: nowrap;
  }
  .holder-name {
    position: absolute;
    left: 60px;
    top: 500px;
    margin: 0;
    font-family: "Open Sans", sans-serif;
    font-weight: 400;
    font-size: 40px;
    color: var(--ink-white);
    white-space: nowrap;
  }
  .divider {
    position: absolute;
    left: 485px;
    top: 400px;
    width: 1px;
    height: 160px;
    background: var(--ink-white);
    opacity: 0.8;
  }
  .contact-list {
    position: absolute;
    left: 510px;
    top: 400px;
    margin: 0;
    padding: 0;
    list-style: none;
    font-family: "Open Sans", sans-serif;
    font-size: 24px;
    color: var(--ink-white);
  }
  .contact-list li {
    display: flex;
    align-items: center;
    gap: 14px;
    height: 44px;
    white-space: nowrap;
  }
  .contact-icon {
    width: 22px;
    height: 22px;
    flex: none;
  }
</style>
</head>
<body>
  <div class="card">
    <svg class="card-wave" viewBox="0 0 1050 600" width="1050" height="600" aria-hidden="true">
      <path fill="var(--brand-sky)" d="M0,440 C300,400 560,290 760,240 C880,210 980,200 1050,195 L1050,600 L0,600 Z"/>
      <path fill="var(--ink-white)" d="M0,462 C300,422 560,312 760,262 C880,232 980,222 1050,217 L1050,600 L0,600 Z"/>
      <path fill="var(--brand-blue)" d="M0,470 C300,430 560,320 760,270 C880,240 980,230 1050,225 L1050,600 L0,600 Z"/>
    </svg>

    <div class="fish-mark" role="img" aria-label="Cartoon fish mascot illustration"></div>
    <h1 class="company-name">Tall Pine Computing</h1>

    <p class="holder-name">Marcus Dellingham</p>
    <div class="divider"></div>

    <ul class="contact-list">
      <li>
        <svg class="contact-icon" viewBox="0 0 22 22" aria-hidden="true">
          <rect width="22" height="22" rx="3" fill="var(--ink-white)"/>
          <path d="M7 5 L9 5 L10 8 L8.6 9.2 C9.4 11 10.8 12.5 12.8 13.4 L14 12 L17 13 L17 15 C17 16 16 17 15 17 C10 16.5 5.5 12 5 7 C5 6 6 5 7 5 Z" fill="var(--brand-blue)"/>
        </svg>
        <span>+1 604 555 0182</span>
      </li>
      <li>
        <svg class="contact-icon" viewBox="0 0 22 22" aria-hidden="true">
          <rect width="22" height="22" rx="3" fill="var(--ink-white)"/>
          <circle cx="11" cy="11" r="6" fill="none" stroke="var(--brand-blue)" stroke-width="1.6"/>
          <path d="M5 11 H17 M11 5 C8.5 8 8.5 14 11 17 M11 5 C13.5 8 13.5 14 11 17" fill="none" stroke="var(--brand-blue)" stroke-width="1.3"/>
        </svg>
        <span>www.tallpinecomputing.com</span>
      </li>
      <li>
        <svg class="contact-icon" viewBox="0 0 22 22" aria-hidden="true">
          <rect width="22" height="22" rx="3" fill="var(--ink-white)"/>
          <path d="M11 4 C8 4 6.5 6.2 6.5 8.5 C6.5 11.5 11 17.5 11 17.5 C11 17.5 15.5 11.5 15.5 8.5 C15.5 6.2 14 4 11 4 Z" fill="var(--brand-blue)"/>
          <circle cx="11" cy="8.6" r="1.8" fill="var(--ink-white)"/>
        </svg>
        <span>2840 Cedar Row, Fernvale, BC</span>
      </li>
    </ul>
  </div>
</body>
</html>
```